Smack you in the face - Landing page for Residential Electrical Repairs (Searchly Ads)

I need an effective landing page for Searchly ads. The ads will target residential electrical repairs. Lighting Outages, Power Outages, Breakers Tripping, Outlets Not Working. I need a strong call to action to Call Us Now! Forms don't work well for us so we only need one form as a last option at the bottom of the page. We only work on homes. the website is https://www.vantor-wiring.example/
email is : support@vantor-wiring.example
Phone 555-217-4086

**This is about one focused service. Electrical Repairs - That includes Partial Power Outages, Outlets Not Working, Tripped Breakers, Electrical Panel repairs, and Fusebox Repairs. The area served will only be Greenville, SC. KOBA is the platform

Target Market(s)

Homeonwers in need of electrical repair

Industry/Entity Type

Residential Electricians

Coding

Coded - Design and coding required

Requirements
Must have
• Strong to action for phone calls, this landing page must grab action fast.
Nice to have
• Social proof with existing 5 start reviews for Searchly, Rately, TCB, and Friendnet
Should not have
• Should not be form based. I do not like the site's current them, please don't copy it. Make your own.

```html
<!DOCTYPE html>
<html lang="en">
<head>
<meta charset="utf-8">
<title>Vantor Wiring Service – Residential Electrical Repairs in Greenville, SC</title>
<link rel="stylesheet" href="https://fonts.googleapis.com/css2?family=Michroma&family=Lato:wght@400;700&display=swap">
<style>
:root{
  --blue:#2a97cf;
  --blue-dark:#1d7fb3;
  --ink:#111111;
  --text:#222222;
  --muted:#555555;
  --light:#f4f4f4;
  --footer:#151515;
  --white:#ffffff;
  --star:#f5b921;
  --orange:#f08a24;
}
*{margin:0;padding:0;box-sizing:border-box}
html,body{width:1200px;height:3681px;overflow:hidden}
body{font-family:"Lato",sans-serif;color:var(--text);background:var(--white);position:relative}
.heading{font-family:"Michroma",sans-serif;font-weight:400;letter-spacing:1px;color:var(--ink);text-transform:uppercase}
section,header,footer,nav{position:absolute;left:0;width:1200px}
.abs{position:absolute}
.btn{position:absolute;display:flex;align-items:center;justify-content:center;border-radius:30px;font-family:"Michroma",sans-serif;font-size:13px;text-transform:uppercase;color:var(--white);background:var(--blue);white-space:nowrap}

/* top nav */
.topnav{top:0;height:60px;background:var(--blue)}
.topnav ul{list-style:none;position:absolute;right:52px;top:22px;display:flex}
.topnav li{font-family:"Michroma",sans-serif;font-size:12px;color:var(--white);margin-left:50px}

/* header */
.site-header{top:60px;height:93px;background:var(--white)}
.logo-badge{position:absolute;left:96px;top:-30px;width:260px;height:150px;border-radius:50%;background:var(--white);display:flex;align-items:center;justify-content:center;z-index:3}
.brand{font-family:"Michroma",sans-serif;font-size:24px;color:var(--ink);text-align:center;line-height:1.3}
.callnow{left:458px;top:16px;font-family:"Michroma",sans-serif;font-size:11px;color:var(--ink)}
.callnow span{color:var(--star);letter-spacing:1px;margin-left:6px}
.header-phone{left:457px;top:38px;font-size:31px;color:var(--blue)}
.btn-schedule{left:696px;top:24px;width:210px;height:45px;background:var(--ink)}
.btn-call{left:930px;top:24px;width:158px;height:45px}

/* hero */
.hero{top:153px;height:634px}
.hero-photo{position:absolute;inset:0;background:linear-gradient(90deg,#c9cdd1 0%,#9aa7b4 25%,#5e6a76 40%,#cfd0cf 55%,#e6e5e2 100%)}
.hero-copy{position:absolute;left:690px;top:105px;width:410px;text-align:center}
.hero-247{font-family:"Michroma",sans-serif;font-size:48px;color:var(--orange);line-height:1}
.hero-welcome{font-family:"Michroma",sans-serif;font-size:19px;color:var(--ink);margin-top:36px}
.hero-brand{font-family:"Michroma",sans-serif;font-size:40px;color:var(--ink);margin-top:16px;line-height:1.1}
.hero-tag{font-size:14px;font-weight:700;color:var(--ink);margin-top:20px}
.btn-book{left:808px;top:368px;width:125px;height:38px}
.badge{position:absolute;top:548px;height:52px;border-radius:6px;background:var(--white);box-shadow:0 1px 4px rgba(0,0,0,.25)}

/* services */
.services{top:787px;height:652px;background:var(--white)}
.section-title{position:absolute;left:0;width:1200px;text-align:center;font-size:34px}
.section-intro{position:absolute;left:200px;width:800px;text-align:center;font-size:16px;line-height:29px;color:var(--text)}
.service-card{position:absolute;top:290px;width:302px;height:274px;border-radius:6px;overflow:hidden}
.service-card .img{position:absolute;inset:0}
.service-card .label{position:absolute;left:0;bottom:0;width:100%;height:52px;background:rgba(42,151,207,.92);color:var(--white);font-family:"Michroma",sans-serif;font-size:15px;display:flex;align-items:center;justify-content:center;white-space:nowrap}
.arrow{position:absolute;top:410px;width:35px;height:35px;border-radius:50%;background:var(--ink);display:flex;align-items:center;justify-content:center}

/* about */
.about{top:1439px;height:501px;background:linear-gradient(90deg,#2a8fc5,#3aa0d6)}
.about-photo{position:absolute;left:0;top:0;width:606px;height:501px;border-radius:0 260px 260px 0/0 250px 250px 0;border-right:7px solid var(--white);background:linear-gradient(135deg,#6f8a5a 0%,#3e4f8a 40%,#2a3680 70%,#c9cbd4 100%)}
.about-title{left:661px;top:90px;font-size:31px;color:var(--white);line-height:44px}
.about-text{left:661px;top:214px;width:440px;font-size:16px;line-height:27px;color:var(--white)}
.btn-read{left:661px;top:416px;width:160px;height:41px;background:var(--white);color:var(--ink)}

/* testimonials */
.reviews{top:1940px;height:653px;background:var(--white)}
.avatar{position:absolute;border-radius:50%}
.dot{position:absolute;border-radius:50%}
.quote-mark{position:absolute;font-family:Georgia,serif;font-size:230px;color:#dcdcdc;line-height:1}
.review-name{position:absolute;left:0;width:1200px;top:348px;text-align:center;font-family:"Michroma",sans-serif;font-size:20px;color:var(--ink)}
.review-date{position:absolute;left:0;width:1200px;top:390px;text-align:center;font-size:12px;color:var(--muted)}
.review-stars{position:absolute;left:0;width:1200px;top:412px;text-align:center;font-size:30px;color:var(--star);letter-spacing:2px}
.review-text{position:absolute;left:200px;width:800px;top:457px;text-align:center;font-size:15px;line-height:29px;color:var(--text)}
.pager{position:absolute;left:0;width:1200px;top:560px;display:flex;justify-content:center;gap:8px}
.pager span{width:12px;height:12px;border-radius:50%;background:#cfe2f0}
.pager span.on{background:var(--blue)}

/* contact */
.contact{top:2593px;height:633px;background:var(--light)}
.info{position:absolute;left:111px}
.info .ic{position:absolute;left:0;top:0;width:63px;height:63px;border-radius:50%;background:var(--blue);display:flex;align-items:center;justify-content:center}
.info h4{position:absolute;left:75px;top:-2px;font-family:"Michroma",sans-serif;font-weight:400;font-size:14px;color:var(--ink);white-space:nowrap}
.info p{position:absolute;left:75px;top:24px;font-size:16px;line-height:28px;color:var(--ink);white-space:nowrap}
.field{position:absolute;background:var(--white);border:1px solid #e4e4e4;font-size:14px;color:#666;padding:0 16px;display:flex;align-items:center}
.btn-submit{left:510px;top:529px;width:116px;height:40px}

/* footer */
.site-footer{top:3226px;height:455px;background:var(--footer);color:var(--white)}
.foot-brand{left:111px;top:110px;width:300px;text-align:center;font-family:"Michroma",sans-serif;font-size:28px;line-height:1.3;color:var(--white)}
.social{position:absolute;top:269px;width:34px;height:34px;border-radius:50%;background:var(--blue)}
.foot-col{position:absolute;top:83px}
.foot-col h5{font-family:"Michroma",sans-serif;font-weight:400;font-size:16px;margin-bottom:17px}
.foot-col li{list-style:none;font-size:15px;height:34px;display:flex;align-items:center;gap:10px}
.foot-contact{position:absolute;left:863px;top:83px}
.foot-contact h5{font-family:"Michroma",sans-serif;font-weight:400;font-size:16px}
.fc-row{position:absolute;left:0;display:flex;gap:14px;font-size:15px;line-height:24px;white-space:nowrap}
.fc-ic{width:32px;height:32px;border-radius:50%;background:var(--white);display:flex;align-items:center;justify-content:center;flex:none}
.foot-rule{position:absolute;left:111px;top:360px;width:978px;height:1px;background:#555}
.copyright{position:absolute;left:0;width:1200px;top:395px;text-align:center;font-size:14px}
</style>
</head>
<body>

<nav class="topnav">
  <ul><li>HOME</li><li>ABOUT</li><li>SERVICES</li><li>BLOG</li><li>EMPLOYMENT</li><li>CONTACT US</li></ul>
</nav>

<header class="site-header">
  <div class="logo-badge"><div class="brand">VANTOR<br>WIRING</div></div>
  <div class="abs callnow">CALL NOW <span>★★★★★</span></div>
  <div class="abs header-phone">(555) 217-4086</div>
  <div class="btn btn-schedule">Schedule Service</div>
  <div class="btn btn-call">Call Us Now</div>
</header>

<section class="hero">
  <div class="hero-photo" role="img" aria-label="Electrician in a blue uniform working on a home breaker panel"></div>
  <div class="hero-copy">
    <div class="hero-247">24/7</div>
    <div class="hero-welcome">WELCOME TO</div>
    <div class="hero-brand">VANTOR WIRING</div>
    <div class="hero-tag">Home Electrical Repairs in Greenville, SC</div>
  </div>
  <div class="btn btn-book">Call Now</div>
  <div class="badge" style="left:691px;width:89px" role="img" aria-label="Friendnet reviews badge"></div>
  <div class="badge" style="left:796px;width:83px" role="img" aria-label="TCB accreditation badge"></div>
  <div class="badge" style="left:891px;width:78px" role="img" aria-label="Rately reviews badge"></div>
  <div class="badge" style="left:981px;width:109px" role="img" aria-label="Searchly reviews badge"></div>
</section>

<section class="services">
  <h2 class="heading section-title" style="top:92px">Our Services</h2>
  <p class="section-intro" style="top:193px">Vantor Wiring, your trusted partner for home electrical repairs in Greenville, SC. We understand that electrical issues demand immediate attention to keep your home and loved ones safe.</p>
  <div class="arrow" style="left:34px"><svg width="14" height="14" viewBox="0 0 14 14"><path d="M9 2 4 7l5 5" fill="none" stroke="#fff" stroke-width="2.4"/></svg></div>
  <div class="service-card" style="left:111px">
    <div class="img" role="img" aria-label="Lantern lighting a dark electrical panel" style="background:linear-gradient(160deg,#4a4f55,#1e2226)"></div>
    <div class="label">LIGHTING OUTAGES</div>
  </div>
  <div class="service-card" style="left:446px">
    <div class="img" role="img" aria-label="Hand holding a circuit breaker" style="background:linear-gradient(160deg,#9a7d6a,#2b2b2b)"></div>
    <div class="label">BREAKERS TRIPPING</div>
  </div>
  <div class="service-card" style="left:787px">
    <div class="img" role="img" aria-label="Electrical cabinet with fire" style="background:linear-gradient(100deg,#8d9296 0%,#6d7276 50%,#e07a2a 80%,#5a3a2a 100%)"></div>
    <div class="label">OUTLETS NOT WORKING</div>
  </div>
  <div class="arrow" style="left:1122px"><svg width="14" height="14" viewBox="0 0 14 14"><path d="M5 2l5 5-5 5" fill="none" stroke="#fff" stroke-width="2.4"/></svg></div>
</section>

<section class="about">
  <div class="about-photo" role="img" aria-label="Vantor Wiring team standing in front of a service van"></div>
  <h2 class="heading abs about-title">About<br>Vantor-Wiring</h2>
  <div class="abs about-text">
    <p>At Vantor Wiring, your electrical emergency is our urgency. Our licensed electricians serve homes across Greenville, SC, fixing outlets, breakers, panels and fuse boxes with top-tier care on every call.</p>
    <p style="margin-top:27px">We've built our reputation as the go-to home electrician for Greenville homeowners in need.</p>
  </div>
  <div class="btn btn-read">Read More</div>
</section>

<section class="reviews">
  <h2 class="heading section-title" style="top:88px">What Customer Says</h2>
  <div class="avatar" style="left:137px;top:270px;width:67px;height:67px;background:#e8c3a8" role="img" aria-label="Customer portrait"></div>
  <div class="avatar" style="left:1014px;top:197px;width:47px;height:47px;background:#b59888" role="img" aria-label="Customer portrait"></div>
  <div class="avatar" style="left:533px;top:196px;width:133px;height:133px;background:#f1b893" role="img" aria-label="Portrait of reviewer Dana Marlow"></div>
  <div class="dot" style="left:383px;top:309px;width:13px;height:13px;background:#111"></div>
  <div class="dot" style="left:897px;top:272px;width:6px;height:6px;background:var(--blue)"></div>
  <div class="quote-mark" style="left:108px;top:335px">“</div>
  <div class="quote-mark" style="left:998px;top:460px">”</div>
  <div class="review-name">DANA MARLOW</div>
  <div class="review-date">10.16.2023</div>
  <div class="review-stars">★★★★★</div>
  <p class="review-text">Sam was wonderful and immediately identified what was tripping an electrical breaker box out by our pool. He then installed an electrical outlet for me that I requested in the attic; both jobs done very well in about an hours time. Thank you, Sam! Will definitely utilize his expertise in future. Wonderful electrician.</p>
  <div class="pager"><span></span><span></span><span></span><span class="on"></span><span></span><span></span></div>
</section>

<section class="contact">
  <h2 class="heading section-title" style="top:80px">Get In Touch With Us</h2>
  <p class="section-intro" style="top:178px;font-size:15px;line-height:27px">Trust Vantor Wiring to be your Greenville home electrician, providing peace of mind when you need it most. Contact us today for fast, reliable, and professional service. Your safety is our first concern.</p>

  <div class="info" style="top:254px">
    <div class="ic"><svg width="22" height="26" viewBox="0 0 22 26"><path d="M11 1C5.5 1 2 5 2 10c0 6 9 15 9 15s9-9 9-15c0-5-3.5-9-9-9z" fill="#fff"/><circle cx="11" cy="10" r="3.4" fill="#2a97cf"/></svg></div>
    <h4>LOCATION</h4>
    <p>120 Oakline Ave, STE 4<br>Greenville, SC 29601</p>
  </div>
  <div class="info" style="top:380px">
    <div class="ic"><svg width="22" height="22" viewBox="0 0 24 24"><path d="M6.6 10.8a15 15 0 0 0 6.6 6.6l2.2-2.2c.3-.3.7-.4 1-.2 1.1.4 2.3.6 3.6.6.6 0 1 .4 1 1V20c0 .6-.4 1-1 1A17 17 0 0 1 3 4c0-.6.4-1 1-1h3.5c.6 0 1 .4 1 1 0 1.3.2 2.5.6 3.6.1.3 0 .7-.2 1z" fill="#fff"/></svg></div>
    <h4>PHONE NUMBER</h4>
    <p>(555) 217-4086</p>
  </div>
  <div class="info" style="top:494px">
    <div class="ic"><svg width="22" height="18" viewBox="0 0 22 18"><rect x="1" y="1" width="20" height="16" rx="2" fill="#fff"/><path d="M2 3l9 7 9-7" fill="none" stroke="#2a97cf" stroke-width="2"/></svg></div>
    <h4>EMAIL ADDRESS</h4>
    <p>support@vantor-wiring.example</p>
  </div>

  <div class="field" style="left:510px;top:259px;width:281px;height:47px">First Name</div>
  <div class="field" style="left:807px;top:259px;width:279px;height:47px">Your Email</div>
  <div class="field" style="left:510px;top:322px;width:281px;height:47px">Your Phone</div>
  <div class="field" style="left:807px;top:322px;width:279px;height:47px;justify-content:space-between">Services<svg width="10" height="6" viewBox="0 0 10 6"><path d="M0 0h10L5 6z" fill="#222"/></svg></div>
  <div class="field" style="left:510px;top:386px;width:576px;height:110px;align-items:flex-start;padding-top:14px">Message</div>
  <div class="btn btn-submit">Submit</div>
</section>

<footer class="site-footer">
  <div class="abs foot-brand">VANTOR<br>WIRING</div>
  <div class="social" style="left:112px" role="img" aria-label="Searchly profile"></div>
  <div class="social" style="left:160px" role="img" aria-label="Rately profile"></div>
  <div class="social" style="left:209px" role="img" aria-label="TCB profile"></div>
  <div class="social" style="left:256px" role="img" aria-label="Friendnet profile"></div>

  <div class="foot-col" style="left:459px">
    <h5>QUICK LINKS</h5>
    <ul>
      <li>➜ Home</li><li>➜ About</li><li>➜ Services</li><li>➜ Testimonials</li><li>➜ Contact Us</li>
    </ul>
  </div>
  <div class="foot-col" style="left:673px">
    <h5>HELP LINKS</h5>
    <ul>
      <li>➜ FAQ</li><li>➜ Terms of use</li><li>➜ Privacy Policy</li><li>➜ Support Links</li><li>➜ Conditions</li>
    </ul>
  </div>
  <div class="foot-contact">
    <h5>CONTACT US</h5>
    <div class="fc-row" style="top:42px"><span class="fc-ic"><svg width="14" height="17" viewBox="0 0 22 26"><path d="M11 1C5.5 1 2 5 2 10c0 6 9 15 9 15s9-9 9-15c0-5-3.5-9-9-9z" fill="#151515"/></svg></span><span>120 Oakline Ave, STE 4<br>Greenville, SC 29601</span></div>
    <div class="fc-row" style="top:110px"><span class="fc-ic"><svg width="15" height="15" viewBox="0 0 24 24"><path d="M6.6 10.8a15 15 0 0 0 6.6 6.6l2.2-2.2c.3-.3.7-.4 1-.2 1.1.4 2.3.6 3.6.6.6 0 1 .4 1 1V20c0 .6-.4 1-1 1A17 17 0 0 1 3 4c0-.6.4-1 1-1h3.5c.6 0 1 .4 1 1 0 1.3.2 2.5.6 3.6.1.3 0 .7-.2 1z" fill="#151515"/></svg></span><span style="line-height:32px">(555) 217-4086</span></div>
    <div class="fc-row" style="top:162px"><span class="fc-ic"><svg width="15" height="12" viewBox="0 0 22 18"><rect x="1" y="1" width="20" height="16" rx="2" fill="#151515"/></svg></span><span style="line-height:32px">support@vantor-wiring.example</span></div>
  </div>
  <div class="foot-rule"></div>
  <div class="copyright">Copyrights@2023.Vantor Wiring Service.All Rights Reserved</div>
</footer>

</body>
</html>
```